Silvermoor Property Development Co.

We need a logo and business card design for a Hong Kong based real estate company, PLX Land. We are want the brand to reflect the owners forward thinking, creative, and trend setting projects, while also reflecting a sense of security and strength. We invest in industrial properties which we convert to co-living or co-working spaces. PLX stands for Greater Bay Area which is the region around southern China including HK, Macau, and 9 other Chinese cities...made up of approx. 68 million people. There are massive infrastructure projects including the bridge to Macau and high-speed rail to SZ and the bridge connecting SZ and Zhongshan.

Target Market(s)

Chinese and western retail investors, as well as institutional investors

Industry/Entity Type

Real Estate Development

Contact Information for Business Card

Dale Whitford
CEO
dale@plxland-example.com
M + 852 9581 4062
F + 852 3864 2217
Suite 2207, The Halvern, 41 Tremont Rd., Central, Hong Kong

Logo Text

plx land (company name) lifestyle property development (underneath)

Colors

Designer to choose colors to be used in the design.

Requirements
Must have
• Details listed above. One side should include the logo and company name...plx land in modern, hip styling with "lifestyle property development"
Nice to have
• Could be a Black card, with metallic purple "plx" and white "land"...but open great design ideas
Should not have
• boring and traditional layout

```html
<!DOCTYPE html>
<html lang="en">
<head>
<meta charset="utf-8">
<title>PLX Land – Business Card</title>
<link rel="stylesheet" href="https://fonts.googleapis.com/css2?family=Open+Sans:wght@400;600;700&family=Arimo:wght@400;700&display=swap">
<style>
  :root {
    --page-bg: #353535;
    --card-top: #2e2e2e;
    --card-bottom: #222222;
    --ink: #ffffff;
    --ink-soft: #c9c9c9;
    --ink-muted: #b5b5b5;
  }
  * { margin: 0; padding: 0; box-sizing: border-box; }
  html, body {
    width: 1042px; height: 1200px; overflow: hidden;
    background: var(--page-bg);
    font-family: "Open Sans", sans-serif;
    color: var(--ink);
  }
  .canvas { position: relative; width: 1042px; height: 1200px; }
  .card {
    position: absolute; left: 170px; width: 714px; height: 420px;
    border-radius: 22px;
    background: radial-gradient(ellipse at 50% 20%, var(--card-top), var(--card-bottom) 75%);
    box-shadow: 0 4px 14px rgba(0,0,0,.45);
  }
  .card--front { top: 126px; }
  .card--back { top: 616px; }

  .brand-lockup {
    position: absolute; left: 0; right: 0; top: 146px;
    text-align: center; white-space: nowrap;
  }
  .brand-name {
    font-weight: 700; font-size: 54px; line-height: 1;
    letter-spacing: -.5px; color: var(--ink);
  }
  .brand-tagline {
    margin-top: 8px;
    font-weight: 700; font-size: 13px; letter-spacing: .6px;
    color: var(--ink-soft);
  }
  .address {
    position: absolute; left: 0; right: 0; top: 356px;
    text-align: center; font-weight: 600; font-size: 17.6px; white-space: nowrap;
  }

  .back-brand {
    position: absolute; left: 118px; top: 200px; width: 190px;
    display: flex; align-items: center; gap: 9px; white-space: nowrap;
    font-weight: 700; font-size: 34px; line-height: 1; color: var(--ink);
  }
  .back-brand .mark {
    flex: none; width: 12px; height: 12px; background: var(--ink);
  }
  .divider {
    position: absolute; left: 329px; top: 128px;
    width: 3px; height: 180px; background: var(--ink);
  }
  .person { position: absolute; left: 358px; top: 124px; white-space: nowrap; }
  .person-name {
    font-family: "Arimo", sans-serif; font-size: 30px; line-height: 1;
    letter-spacing: .3px;
  }
  .person-name .first { font-weight: 700; }
  .person-name .last { font-weight: 400; color: var(--ink-muted); }
  .person-role {
    display: flex; align-items: center; gap: 10px; margin-top: 6px;
    font-family: "Arimo", sans-serif; font-weight: 700; font-size: 21px; letter-spacing: 2px;
  }
  .person-role .rule { width: 150px; height: 2px; background: var(--ink); }

  .contacts { position: absolute; left: 360px; top: 218px; list-style: none; white-space: nowrap; }
  .contacts li {
    display: flex; align-items: center; gap: 14px;
    font-size: 22px; height: 31px;
  }
  .contacts svg { width: 16px; height: 16px; fill: var(--ink); }
</style>
</head>
<body>
<main class="canvas">
  <section class="card card--front">
    <div class="brand-lockup">
      <div class="brand-name">PLX Land</div>
      <div class="brand-tagline">lifestyle property development</div>
    </div>
    <p class="address">Suite 2207, The Halvern, 41 Tremont Rd, Central, Hong Kong</p>
  </section>

  <section class="card card--back">
    <div class="back-brand"><span class="mark"></span>PLX Land</div>
    <div class="divider"></div>
    <div class="person">
      <div class="person-name"><span class="first">DALE</span> <span class="last">WHITFORD</span></div>
      <div class="person-role">CEO <span class="rule"></span></div>
    </div>
    <ul class="contacts">
      <li>
        <svg viewBox="0 0 16 16" aria-hidden="true"><path d="M3.2 1.5l2.3 2.8-1.3 1.6c.9 2 2.3 3.4 4.3 4.4l1.6-1.3 2.8 2.3-1.4 2.2C6.6 13.2 2.8 9.4 1.4 3z"/></svg>
        852 9581 4062
      </li>
      <li>
        <svg viewBox="0 0 16 16" aria-hidden="true"><rect x="4" y="1.5" width="8" height="4"/><rect x="1.5" y="6" width="13" height="6" rx="1.5"/><rect x="4" y="10" width="8" height="4.5" fill="#2a2a2a" stroke="#fff" stroke-width="1.2"/></svg>
        852 3864 2217
      </li>
      <li>
        <svg viewBox="0 0 16 16" aria-hidden="true"><path d="M1 3h14v10H1z M1.8 3.6L8 8.6l6.2-5" stroke="#2a2a2a" stroke-width="1.2"/></svg>
        dale@plxland-example.com
      </li>
    </ul>
  </section>
</main>
</body>
</html>
```